Design a Website in Wordpress for an Australian Health Training Company in Health related courses

We require a WORDPRESS based Website (due to add on's we need to use for third party software) to replace our old site.
We offer national face to face delivery in medical reception, terminology and also administration.
The website will have around 6 pages and the ability to describe our main 6 courses (perhaps on the Courses page this may be tabs opening up to details for example?)
I have attached a previous sample of a Joomla site which was being developed (please do not feel you have to copy this - but I am just giving it as a sample - copying would be boring). But it gives an idea of look/feel and colours which may be suitable. Open to other ideas though.
I will provide some of the content, but would like the ability to finish the content myself.
Images and graphics are important. While a few medical photos re great - don't be tempted to us all pictures of doctors and nurses (although a couple would be good) - these are administrative courses so general corporate, eye catching visionary pictures of people in general are great. A medical type picture is also fine.
THE BOOKING system - will be via an ADD ON which will occur at the end of the project and is supplied by a third party software company (our student management system). This project will include up to 2 hours working with the Tech guys from the third party software to enable the ADD ON. If this ADD ON requires more time, we will pay hourly (although I do not expect it will).
Target Market(s)
Mostly a female market, many mature aged women target 25-45 yrs. Mixture of medical/health and corporate. Maybe a bit of mums returning to work and corporate inspiration.
Industry/Entity Type
It Company
Coding
Coded - Design and coding required
Number of Pages Required
5+ page
Requirements
Must have
- Wordpress
- Great graphics
- Interesting
- professional and clean
- Enquiry section (info Pak)
- Should have a University feel to it - Education
- Pages
- Home Page - About Us - Recruitment -Courses - Class Schedule - Traineeships Queensland Funding - Latest News Blog - Corporate Training- Contact us

```html
<!DOCTYPE html>
<html lang="en">
<head>
<meta charset="utf-8">
<title>Harlow Institute of Training</title>
<link href="https://fonts.googleapis.com/css2?family=Open+Sans:ital,wght@0,400;0,600;0,700;1,400;1,600&family=Roboto:wght@400;500;700&family=Roboto+Condensed:wght@400;700&display=swap" rel="stylesheet">
<style>
:root{
  --navy:#2c3d59;
  --navy-deep:#233149;
  --navy-bar:#1f2b40;
  --ink:#2b2f36;
  --text:#5a5f66;
  --muted:#8a9099;
  --blue:#2f4b73;
  --tan:#d29d69;
  --tan-btn:#d08f59;
  --light:#f3f4f6;
  --line:#dfe2e6;
  --white:#ffffff;
}
*{box-sizing:border-box;margin:0;padding:0}
html,body{width:1200px;height:2839px;overflow:hidden}
body{position:relative;font-family:'Open Sans',Arial,sans-serif;color:var(--text);background:var(--white)}
h1,h2,h3,h4{font-family:'Roboto',Arial,sans-serif;font-weight:500}

/* top bar */
.topbar{position:absolute;left:0;top:0;width:1200px;height:30px;background:var(--navy-bar);color:var(--white);font-size:12px}
.topbar .socials{position:absolute;left:100px;top:9px;display:flex;gap:6px}
.topbar .socials span{width:12px;height:12px;background:var(--white);border-radius:2px;display:block}
.topbar .search{position:absolute;left:224px;top:8px}
.topbar .divider{position:absolute;top:0;width:1px;height:30px;background:#3a4862}
.topbar .contact{position:absolute;top:7px;display:flex;align-items:center;gap:8px}

/* header */
.site-header{position:absolute;left:0;top:30px;width:1200px;height:125px;background:var(--white);border-bottom:1px solid var(--line)}
.brand{position:absolute;left:98px;top:22px;width:110px;text-align:center;font-family:'Roboto',Arial,sans-serif;font-weight:700;font-size:13px;line-height:15px;color:var(--navy)}
.brand-mark{display:block;width:34px;height:34px;margin:8px auto 0;background:var(--navy)}
.main-nav{position:absolute;left:0;top:58px;width:1000px;height:16px;font-family:'Roboto Condensed',Arial,sans-serif;font-size:11.5px;color:var(--ink);text-transform:uppercase;white-space:nowrap}
.main-nav a{position:absolute;top:0;color:inherit;text-decoration:none}
.header-btn{position:absolute;left:1020px;width:80px;height:28px;border:1px solid var(--navy);border-radius:3px;font-family:'Roboto Condensed',Arial,sans-serif;font-size:11px;color:var(--navy);text-align:center;line-height:26px;font-weight:700}

/* hero */
.hero{position:absolute;left:0;top:155px;width:1200px;height:494px}
.hero-photo{position:absolute;inset:0;background:linear-gradient(90deg,#eef1f5 0%,#e3e8ee 40%,#c9d1db 70%,#b8c0c9 100%)}
.hero h1{position:absolute;left:100px;top:128px;font-size:38px;line-height:42px;font-weight:700;color:var(--navy);font-family:'Roboto Condensed',Arial,sans-serif}
.hero p{position:absolute;left:100px;top:228px;width:385px;font-size:12.5px;line-height:20px;color:#4d535c}
.btn-dark{position:absolute;left:100px;top:311px;width:137px;height:39px;background:var(--navy);color:var(--white);font-family:'Roboto',Arial,sans-serif;font-size:14px;font-weight:500;display:flex;align-items:center;justify-content:center;gap:8px;border-radius:2px}
.hero-arrow{position:absolute;top:212px}

/* courses */
.courses{position:absolute;left:0;top:649px;width:1200px;height:392px;background:var(--navy)}
.courses h2{position:absolute;left:0;top:40px;width:1200px;text-align:center;color:var(--white);font-size:28px;font-weight:400}
.course{position:absolute;top:110px;width:240px;text-align:center;color:var(--white)}
.course-icon{width:114px;height:114px;border-radius:50%;background:var(--white);margin:0 auto;display:flex;align-items:center;justify-content:center}
.course h3{margin-top:26px;font-size:14px;font-weight:500;text-transform:uppercase}
.course p{margin-top:8px;font-size:11.5px;line-height:17px;color:#dfe4ec;padding:0 8px}
.course .chev{margin-top:10px}

/* why */
.why h2{position:absolute;left:0;top:1090px;width:1200px;text-align:center;font-size:30px;color:var(--ink);font-weight:400}
.why-card{position:absolute;top:1168px;width:235px;text-align:center}
.why-photo{width:235px;height:184px}
.why-card h3{margin-top:16px;font-size:15.5px;font-weight:400;color:#4a4f57}
.why-card p{margin-top:6px;font-size:11.5px;line-height:17px;color:var(--text)}

/* welcome */
.welcome{position:absolute;left:0;top:1530px;width:1200px;height:429px;background:var(--light);border-top:1px solid var(--line)}
.welcome-brand{position:absolute;left:51px;top:120px;width:252px;text-align:center;font-family:'Roboto',Arial,sans-serif;font-weight:700;font-size:22px;line-height:28px;color:var(--navy)}
.welcome h3{position:absolute;left:339px;top:60px;font-size:24px;font-weight:400;color:var(--ink)}
.welcome h2{position:absolute;left:339px;top:96px;font-size:28px;font-weight:400;color:var(--blue)}
.welcome .rule{position:absolute;left:339px;top:146px;width:360px;height:1px;background:var(--line)}
.welcome .copy{position:absolute;left:339px;top:172px;width:385px;font-size:11px;line-height:19px;color:var(--text)}
.welcome .copy p+p{margin-top:8px}
.read-more{display:flex;align-items:center;gap:8px;font-family:'Roboto',Arial,sans-serif;font-weight:500;color:var(--ink);font-size:13px}
.welcome .read-more{position:absolute;left:343px;top:342px}
.enquiry{position:absolute;left:816px;top:46px;width:284px}
.enquiry h3{position:static;font-size:24px;font-weight:400;color:var(--ink);margin-bottom:14px}
.field{height:42px;background:var(--white);border:1px solid var(--line);margin-bottom:9px;font-size:11.5px;color:#6d727a;display:flex;align-items:center;justify-content:space-between;padding:0 14px}
.submit{margin-top:22px;width:148px;height:38px;background:var(--tan-btn);color:var(--white);font-family:'Roboto',Arial,sans-serif;font-weight:700;font-size:13px;display:flex;align-items:center;justify-content:center;border-radius:2px}

/* testimonial */
.testimonial{position:absolute;left:0;top:1959px;width:1200px;height:212px;background:var(--tan)}
.testimonial h2{position:absolute;left:98px;top:88px;font-size:34px;font-weight:500;color:var(--white);font-family:'Roboto Condensed',Arial,sans-serif}
.avatar{position:absolute;left:337px;top:51px;width:110px;height:110px;border-radius:50%;background:linear-gradient(180deg,#c9cdd3,#8d949f);border:4px solid var(--white)}
.quote{position:absolute;left:473px;top:46px;width:640px;font-style:italic;color:var(--white);font-size:12.5px;line-height:19px}
.quote-name{position:absolute;left:473px;top:124px;font-style:italic;color:var(--white);font-size:16px;font-weight:600}
.quote-dots{position:absolute;left:470px;top:162px;display:flex;gap:4px}
.quote-dots span{width:11px;height:11px;border-radius:50%;background:var(--white)}

/* news */
.news h2{position:absolute;left:98px;top:2218px;font-size:24px;font-weight:400;color:var(--ink)}
.news .rule{position:absolute;left:98px;top:2266px;width:1004px;height:1px;background:var(--line)}
.news-arrows{position:absolute;left:1068px;top:2222px}
.news-item{position:absolute;top:2306px;width:275px}
.date{position:absolute;left:0;top:0;width:42px;text-align:center;font-size:12px}
.date .day{background:var(--navy);color:var(--white);height:20px;line-height:20px}
.date .mon{background:#e7e9ec;color:var(--ink);height:25px;line-height:25px}
.news-item h3{position:absolute;left:52px;top:4px;width:220px;font-size:15.5px;line-height:23px;font-weight:400;color:#7a8fa8}
.news-item p{position:absolute;left:0;top:64px;width:275px;font-size:11px;line-height:19px;color:var(--text)}
.news-item .read-more{position:absolute;left:0;top:138px;font-size:11.5px}

/* footer */
.site-footer{position:absolute;left:0;top:2512px;width:1200px;height:267px;background:var(--navy);color:var(--white)}
.site-footer h4{position:absolute;top:34px;font-size:19px;font-weight:500}
.quick-links{position:absolute;left:98px;top:91px;list-style:none;font-size:12px;line-height:24px}
.news-copy{position:absolute;left:390px;top:80px;width:240px;font-size:12px;line-height:19px}
.news-input{position:absolute;left:390px;top:133px;width:226px;height:40px;background:var(--white);color:#555;font-size:11.5px;padding:0 12px;display:flex;align-items:center}
.subscribe{position:absolute;left:390px;top:184px;width:93px;height:36px;background:var(--navy-bar);font-size:11px;display:flex;align-items:center;justify-content:center}
.contact-block{position:absolute;left:685px;top:80px;font-size:12px;line-height:19px}
.contact-line{position:absolute;left:689px;display:flex;align-items:center;gap:14px;font-size:12.5px}
.footer-socials{position:absolute;left:685px;top:196px;display:flex;gap:6px}
.footer-socials span{width:21px;height:21px;border:1px solid var(--white);border-radius:50%}
.footer-brand{position:absolute;left:908px;top:100px;width:190px;text-align:center;font-family:'Roboto',Arial,sans-serif;font-weight:700;font-size:19px;line-height:25px;color:var(--white)}
.bottom-bar{position:absolute;left:0;top:2779px;width:1200px;height:60px;background:var(--navy-bar);color:#d6dbe3;font-size:11.5px;text-align:center;line-height:60px}
</style>
</head>
<body>

<div class="topbar">
  <div class="socials"><span></span><span></span><span></span><span></span></div>
  <svg class="search" width="13" height="13" viewBox="0 0 13 13"><circle cx="5.5" cy="5.5" r="4" fill="none" stroke="#fff" stroke-width="1.8"/><line x1="8.5" y1="8.5" x2="12" y2="12" stroke="#fff" stroke-width="1.8"/></svg>
  <div class="divider" style="left:680px"></div>
  <div class="contact" style="left:698px">
    <svg width="12" height="12" viewBox="0 0 12 12"><path d="M2 1h3l1 3-2 1a7 7 0 0 0 3 3l1-2 3 1v3c-6 0-9-3-9-9z" fill="#fff"/></svg>
    <span>555-010-2040</span>
  </div>
  <div class="divider" style="left:836px"></div>
  <div class="contact" style="left:846px">
    <svg width="13" height="10" viewBox="0 0 13 10"><rect x="0.5" y="0.5" width="12" height="9" fill="none" stroke="#fff"/><path d="M0.5 0.5l6 5 6-5" fill="none" stroke="#fff"/></svg>
    <span>Email: info@harlowtraining.example</span>
  </div>
</div>

<header class="site-header">
  <div class="brand">HARLOW<br>INSTITUTE<br>OF TRAINING<span class="brand-mark"></span></div>
  <nav class="main-nav">
    <a style="left:269px">Home</a>
    <a style="left:327px">About Us</a>
    <a style="left:406px">Recruitment</a>
    <a style="left:501px">Courses</a>
    <a style="left:577px">Class Schedule</a>
    <a style="left:689px">Traineeships</a>
    <a style="left:787px">Blog</a>
    <a style="left:844px">Corporate</a>
    <a style="left:932px">Contact Us</a>
  </nav>
  <div class="header-btn" style="top:32px">ENROL NOW</div>
  <div class="header-btn" style="top:68px">INFO PACK</div>
</header>

<section class="hero">
  <div class="hero-photo" role="img" aria-label="Photo of a trainer presenting at a flip chart to a group of attentive students in a bright classroom"></div>
  <h1>HARLOW INSTITUTE<br>OF TRAINING</h1>
  <p>Duis aute irure dolor in reprehenderit in voluptate velit esse cillum dolore eu fugiat nulla pariatur. Excepteur sint occaecat cupidatat non proident, sunt</p>
  <div class="btn-dark">MORE INFO
    <svg width="13" height="13" viewBox="0 0 13 13"><circle cx="6.5" cy="6.5" r="6.5" fill="#fff"/><path d="M5 3.5l3 3-3 3" fill="none" stroke="#2c3d59" stroke-width="1.8"/></svg>
  </div>
  <svg class="hero-arrow" style="left:20px" width="20" height="56" viewBox="0 0 20 56"><path d="M18 2L3 28l15 26" fill="none" stroke="#3b4656" stroke-width="2"/></svg>
  <svg class="hero-arrow" style="left:1140px" width="20" height="56" viewBox="0 0 20 56"><path d="M2 2l15 26L2 54" fill="none" stroke="#ffffff" stroke-width="2"/></svg>
</section>

<section class="courses">
  <h2>LIST OF COURSES</h2>
  <div class="course" style="left:84px">
    <div class="course-icon">
      <svg width="54" height="54" viewBox="0 0 54 54" fill="none" stroke="#2c3d59" stroke-width="4" stroke-linecap="round"><path d="M12 6v14a10 10 0 0 0 20 0V6"/><path d="M22 30v6a10 10 0 0 0 20 0v-8"/><circle cx="42" cy="22" r="5"/></svg>
    </div>
    <h3>Medical Terminology</h3>
    <p>Nemo enim ipsam voluptatem quia volut sit aspernatur aut odit aut fugit</p>
    <svg class="chev" width="14" height="14" viewBox="0 0 14 14" fill="none" stroke="#fff" stroke-width="1.8"><path d="M2 2l5 5 5-5M2 7l5 5 5-5"/></svg>
  </div>
  <div class="course" style="left:349px">
    <div class="course-icon">
      <svg width="58" height="44" viewBox="0 0 58 44"><path d="M29 2v8" stroke="#2c3d59" stroke-width="3" fill="none"/><rect x="2" y="12" width="54" height="30" rx="5" fill="#2c3d59"/><g fill="#fff"><rect x="8" y="18" width="6" height="5"/><rect x="17" y="18" width="6" height="5"/><rect x="26" y="18" width="6" height="5"/><rect x="35" y="18" width="6" height="5"/><rect x="44" y="18" width="6" height="5"/><rect x="8" y="26" width="6" height="5"/><rect x="17" y="26" width="6" height="5"/><rect x="26" y="26" width="6" height="5"/><rect x="35" y="26" width="6" height="5"/><rect x="44" y="26" width="6" height="5"/><rect x="14" y="34" width="30" height="4"/></g></svg>
    </div>
    <h3>Keyboard and Typing</h3>
    <p>Nemo enim ipsam voluptatem quia volut sit aspernatur aut odit aut fugit</p>
    <svg class="chev" width="14" height="14" viewBox="0 0 14 14" fill="none" stroke="#fff" stroke-width="1.8"><path d="M2 2l5 5 5-5M2 7l5 5 5-5"/></svg>
  </div>
  <div class="course" style="left:616px">
    <div class="course-icon">
      <svg width="52" height="52" viewBox="0 0 52 52"><circle cx="26" cy="26" r="24" fill="#2c3d59"/><path d="M14 14c6 2 8 6 5 10s2 8 6 10l-2 10M32 6c-2 6 2 8 6 8s6 6 4 12c-4-2-8 2-6 8" fill="none" stroke="#fff" stroke-width="2.5"/></svg>
    </div>
    <h3>Harlow Online</h3>
    <p>Nemo enim ipsam voluptatem quia volut sit aspernatur aut odit aut fugit</p>
    <svg class="chev" width="14" height="14" viewBox="0 0 14 14" fill="none" stroke="#fff" stroke-width="1.8"><path d="M2 2l5 5 5-5M2 7l5 5 5-5"/></svg>
  </div>
  <div class="course" style="left:872px">
    <div class="course-icon">
      <svg width="56" height="50" viewBox="0 0 56 50" fill="#2c3d59"><circle cx="20" cy="10" r="8"/><path d="M6 34c0-10 6-14 14-14s12 4 14 10H6z"/><rect x="30" y="16" width="20" height="14" rx="1"/><rect x="2" y="34" width="52" height="6"/><rect x="6" y="40" width="4" height="10"/><rect x="46" y="40" width="4" height="10"/></svg>
    </div>
    <h3>Medical Reception</h3>
    <p>Nemo enim ipsam voluptatem quia volut sit aspernatur aut odit aut fugit</p>
    <svg class="chev" width="14" height="14" viewBox="0 0 14 14" fill="none" stroke="#fff" stroke-width="1.8"><path d="M2 2l5 5 5-5M2 7l5 5 5-5"/></svg>
  </div>
</section>

<section class="why">
  <h2>WHY HARLOW INSTITUTE ?</h2>
  <div class="why-card" style="left:98px">
    <div class="why-photo" role="img" aria-label="Photo of a smiling woman writing on a whiteboard beside two colleagues" style="background:linear-gradient(135deg,#e8e6e2,#b9b4ad)"></div>
    <h3>Quality</h3>
    <p>Harlow delivers quality, effective training facilitated by industry leaders. Just ask our students who rate us on average of 4.7 out of 5</p>
  </div>
  <div class="why-card" style="left:356px">
    <div class="why-photo" role="img" aria-label="Photo of business people in suits working together at a meeting table" style="background:linear-gradient(135deg,#c9d2dc,#5e6b7c)"></div>
    <h3>Experience</h3>
    <p>Harlow is Australia's largest and leading providers of nationally recognised training in health administration – training from over 17 locations Australia wide.</p>
  </div>
  <div class="why-card" style="left:610px">
    <div class="why-photo" role="img" aria-label="Photo of three professionals discussing work around a laptop in an office" style="background:linear-gradient(135deg,#eef1f4,#8893a0)"></div>
    <h3>Value</h3>
    <p>Our innovative teaching approach allows us to deliver exceptional training at affordable prices with no hidden extras.</p>
  </div>
  <div class="why-card" style="left:865px">
    <div class="why-photo" role="img" aria-label="Photo of a hand in a business suit touching glowing blue gears on a dark background" style="background:linear-gradient(135deg,#2f3a48,#0f141b)"></div>
    <h3>Industry Recognised</h3>
    <p>Harlow work hand in hand with industry to develop our core programme and consolidate the programme annually to keep the programme fresh and relevant.</p>
  </div>
</section>

<section class="welcome">
  <div class="welcome-brand">HARLOW<br>INSTITUTE<br>OF TRAINING</div>
  <h3>WELCOME TO</h3>
  <h2>HARLOW INSTITUTE OF TRAINING</h2>
  <div class="rule"></div>
  <div class="copy">
    <p>Harlow is Australia's Leading Provider of Educational, Training and Support Services for the Medical and Dental industry - enabling students to be immediately skilled and 'Job Ready' for a career in Health.</p>
    <p>Harlow is a Registered Training Organisation offering specialised Medical Administration Training in over 15 locations Australia wide. Harlow have trained thousands of students the required knowledge and skills to become successful health care administrators.</p>
  </div>
  <div class="read-more">READ MORE
    <svg width="12" height="12" viewBox="0 0 13 13"><circle cx="6.5" cy="6.5" r="6.5" fill="#2b2f36"/><path d="M5 3.5l3 3-3 3" fill="none" stroke="#fff" stroke-width="1.8"/></svg>
  </div>
  <div class="enquiry">
    <h3>ENQUIRY</h3>
    <div class="field">Your Name</div>
    <div class="field">E-mail</div>
    <div class="field">Course <svg width="8" height="5" viewBox="0 0 8 5"><path d="M0 0h8L4 5z" fill="#666"/></svg></div>
    <div class="field">State <svg width="8" height="5" viewBox="0 0 8 5"><path d="M0 0h8L4 5z" fill="#666"/></svg></div>
    <div class="field">Mobile</div>
    <div class="submit">SUBMIT ENQUIRY</div>
  </div>
</section>

<section class="testimonial">
  <h2>TESTIMONIAL</h2>
  <div class="avatar" role="img" aria-label="Portrait photo of a student"></div>
  <p class="quote">" I want to say a huge thank you for the course and knowledge I came away with. I have secured a fantastic job after my first application! Such good value for money too! I would highly recommend it. I'm a mature age person so it's never too late to up-skill yourself to get what you deserve!</p>
  <div class="quote-name">Clara Bennet - Harlow Institute of Training</div>
  <div class="quote-dots"><span></span><span></span></div>
</section>

<section class="news">
  <h2>LATEST NEWS</h2>
  <svg class="news-arrows" width="34" height="16" viewBox="0 0 34 16" fill="none" stroke="#2b2f36" stroke-width="2"><path d="M8 2L2 8l6 6M26 2l6 6-6 6"/></svg>
  <div class="rule"></div>
  <article class="news-item" style="left:98px">
    <div class="date"><div class="day">03</div><div class="mon">Sep</div></div>
    <h3>Nemo enim ipsam volup quia voluptas sit</h3>
    <p>Lorem ipsum dolor sit amet, consectetur adipiscing elit, sed do eiusmod tempor incididunt ut labore et dolore magna aliqua. Ut enim ad minim</p>
    <div class="read-more">READ MORE <svg width="11" height="11" viewBox="0 0 13 13"><circle cx="6.5" cy="6.5" r="6.5" fill="#2b2f36"/><path d="M5 3.5l3 3-3 3" fill="none" stroke="#fff" stroke-width="1.8"/></svg></div>
  </article>
  <article class="news-item" style="left:467px">
    <div class="date"><div class="day">03</div><div class="mon">Sep</div></div>
    <h3>Nemo enim ipsam volup quia voluptas sit</h3>
    <p>Lorem ipsum dolor sit amet, consectetur adipiscing elit, sed do eiusmod tempor incididunt ut labore et dolore magna aliqua. Ut enim ad minim</p>
    <div class="read-more">READ MORE <svg width="11" height="11" viewBox="0 0 13 13"><circle cx="6.5" cy="6.5" r="6.5" fill="#2b2f36"/><path d="M5 3.5l3 3-3 3" fill="none" stroke="#fff" stroke-width="1.8"/></svg></div>
  </article>
  <article class="news-item" style="left:829px">
    <div class="date"><div class="day">03</div><div class="mon">Sep</div></div>
    <h3>Nemo enim ipsam volup quia voluptas sit</h3>
    <p>Lorem ipsum dolor sit amet, consectetur adipiscing elit, sed do eiusmod tempor incididunt ut labore et dolore magna aliqua. Ut enim ad minim</p>
    <div class="read-more">READ MORE <svg width="11" height="11" viewBox="0 0 13 13"><circle cx="6.5" cy="6.5" r="6.5" fill="#2b2f36"/><path d="M5 3.5l3 3-3 3" fill="none" stroke="#fff" stroke-width="1.8"/></svg></div>
  </article>
</section>

<footer class="site-footer">
  <h4 style="left:98px">Quick Links</h4>
  <ul class="quick-links">
    <li>About us</li><li>Recruitment</li><li>Courses</li><li>Class Schedule</li><li>Traineeships Queensland Funding</li><li>Corporate Training- Contact us</li>
  </ul>
  <h4 style="left:390px">Sign up for newsletter</h4>
  <p class="news-copy">Excepteur sint occaecat cupidatat non dent, sunt in culpa qui officia</p>
  <div class="news-input">Enter Name</div>
  <div class="subscribe">SUBSCRIBE</div>
  <h4 style="left:685px">Contact Us</h4>
  <p class="contact-block">Harlow Institute of Training<br>No. 4410208, Brisbane QLD</p>
  <div class="contact-line" style="top:126px">
    <svg width="14" height="14" viewBox="0 0 12 12"><path d="M2 1h3l1 3-2 1a7 7 0 0 0 3 3l1-2 3 1v3c-6 0-9-3-9-9z" fill="none" stroke="#fff"/></svg>
    <span>+61 2 5550 1234,</span>
  </div>
  <div class="contact-line" style="top:153px">
    <svg width="14" height="11" viewBox="0 0 13 10"><rect x="0.5" y="0.5" width="12" height="9" fill="none" stroke="#fff"/><path d="M0.5 0.5l6 5 6-5" fill="none" stroke="#fff"/></svg>
    <span>info@harlowhealth.example</span>
  </div>
  <div class="footer-socials"><span></span><span></span><span></span><span></span><span></span></div>
  <div class="footer-brand">HARLOW<br>INSTITUTE<br>OF TRAINING</div>
</footer>

<div class="bottom-bar">©2015 - 2016 HARLOW INSTITUTE OF TRAINING... All Rights Reserved.</div>

</body>
</html>
```